The most modern business card ever !!!

Our company call “Vendalo”. Vendalo is a technology company specialized in cruises solutions. Out main product is a platform to reserve cruises. This is a revolutionary platform that make easier to travel agencies and final users to reserve cruises across dozen companies like tibba, wernu, hpv, dgb, etc..We are a “start up”, with a young team of developers and we want to transmit it.. For it, we want something different, a modern business card that represent cruises and technology.. When someone receive this card, this person should say: wowww this is different… this is modern… this is a cruise related company..
- diferent, modern
- traditions business card

```html
<!DOCTYPE html>
<html lang="en">
<head>
<meta charset="UTF-8">
<title>Vendalo Business Card</title>
<link href="https://fonts.googleapis.com/css2?family=Exo+2:wght@400;500&family=Open+Sans:wght@400&display=swap" rel="stylesheet">
<style>
  :root {
    --page-bg: #1b1c1f;
    --card-bg: #202427;
    --card-edge: #2a2f33;
    --logo-front: #b8bcc1;
    --ink-white: #f2f4f5;
    --accent-blue: #2ea3dd;
    --wave-soft: rgba(46, 163, 221, 0.35);
    --wave-faint: rgba(46, 163, 221, 0.15);
    --divider: #2d6f93;
  }
  * { margin: 0; padding: 0; box-sizing: border-box; }
  html, body {
    width: 1200px;
    height: 800px;
    overflow: hidden;
    background: var(--page-bg);
  }
  .stage {
    width: 1200px;
    height: 800px;
    display: flex;
    align-items: center;
    justify-content: center;
    gap: 40px;
  }
  .card {
    position: relative;
    width: 540px;
    height: 309px;
    border-radius: 16px;
    overflow: hidden;
    background: radial-gradient(ellipse at 30% 20%, #252a2e 0%, var(--card-bg) 60%);
    border: 1px solid var(--card-edge);
    box-shadow: 0 18px 40px rgba(0, 0, 0, 0.45);
  }
  .sea-waves {
    position: absolute;
    left: 0;
    bottom: 0;
    width: 540px;
    height: 70px;
  }
  .card-front .brand-name {
    position: absolute;
    left: 0;
    right: 0;
    top: 118px;
    text-align: center;
    font-size: 64px;
    color: var(--logo-front);
  }
  .brand-name {
    font-family: "Exo 2", sans-serif;
    font-weight: 500;
    letter-spacing: 2px;
    line-height: 1;
  }
  .card-back .brand-name {
    position: absolute;
    left: 46px;
    top: 150px;
    font-size: 52px;
    color: var(--ink-white);
  }
  .divider {
    position: absolute;
    left: 300px;
    top: 64px;
    width: 1px;
    height: 150px;
    background: linear-gradient(to bottom, transparent, var(--divider) 25%, var(--divider) 75%, transparent);
  }
  .contact-block {
    position: absolute;
    left: 326px;
    top: 82px;
  }
  .person-name {
    font-family: "Exo 2", sans-serif;
    font-weight: 400;
    font-size: 22px;
    color: var(--ink-white);
    letter-spacing: 0.5px;
  }
  .person-role {
    font-family: "Open Sans", sans-serif;
    font-size: 12px;
    color: var(--accent-blue);
    margin-top: 1px;
    margin-bottom: 16px;
  }
  .contact-line {
    display: flex;
    align-items: center;
    gap: 8px;
    font-family: "Open Sans", sans-serif;
    font-size: 11px;
    color: var(--ink-white);
    margin-bottom: 8px;
  }
  .contact-icon { width: 16px; height: 16px; flex: none; }
</style>
</head>
<body>
  <main class="stage">
    <section class="card card-front" aria-label="Card front">
      <span class="brand-name">Vendalo</span>
      <svg class="sea-waves" viewBox="0 0 540 70" aria-hidden="true">
        <path d="M0 40 C 90 20, 180 60, 270 40 S 450 20, 540 40" fill="none" stroke="var(--accent-blue)" stroke-width="1.6"/>
        <path d="M0 52 C 90 34, 180 70, 270 52 S 450 34, 540 52" fill="none" stroke="var(--wave-soft)" stroke-width="1.2"/>
        <path d="M0 63 C 90 48, 180 78, 270 63 S 450 48, 540 63" fill="none" stroke="var(--wave-faint)" stroke-width="1"/>
      </svg>
    </section>

    <section class="card card-back" aria-label="Card back">
      <span class="brand-name">Vendalo</span>
      <div class="divider"></div>
      <div class="contact-block">
        <p class="person-name">Nora Fielding</p>
        <p class="person-role">President</p>
        <p class="contact-line">
          <svg class="contact-icon" viewBox="0 0 16 16" aria-hidden="true">
            <circle cx="8" cy="8" r="7.2" fill="none" stroke="var(--accent-blue)" stroke-width="1"/>
            <rect x="5.5" y="3.8" width="5" height="8.4" rx="1" fill="none" stroke="var(--accent-blue)" stroke-width="1"/>
            <line x1="7.3" y1="10.8" x2="8.7" y2="10.8" stroke="var(--accent-blue)" stroke-width="0.9"/>
          </svg>
          +(0) 44 210 7788
        </p>
        <p class="contact-line">
          <svg class="contact-icon" viewBox="0 0 16 16" aria-hidden="true">
            <circle cx="8" cy="8" r="7.2" fill="var(--accent-blue)"/>
            <rect x="4.3" y="5.2" width="7.4" height="5.6" rx="0.6" fill="none" stroke="var(--card-bg)" stroke-width="0.9"/>
            <polyline points="4.5,5.5 8,8.4 11.5,5.5" fill="none" stroke="var(--card-bg)" stroke-width="0.9"/>
          </svg>
          info@vendalomail.com
        </p>
      </div>
      <svg class="sea-waves" viewBox="0 0 540 70" aria-hidden="true">
        <path d="M0 44 C 90 24, 180 64, 270 44 S 450 24, 540 44" fill="none" stroke="var(--accent-blue)" stroke-width="1.6"/>
        <path d="M0 55 C 90 37, 180 73, 270 55 S 450 37, 540 55" fill="none" stroke="var(--wave-soft)" stroke-width="1.2"/>
        <path d="M0 65 C 90 50, 180 80, 270 65 S 450 50, 540 65" fill="none" stroke="var(--wave-faint)" stroke-width="1"/>
      </svg>
    </section>
  </main>
</body>
</html>
```